Yoga/movement guide/teacher for adult yoga practice and kid yoga

What is the positioning or mission statement of your company? to guide individuals in a yoga-based safe and sustainable movement practice applicable to all ages and body types. Currently my focus is working with children in daycare and school settings, but my goal is to expand into private yoga practice for adults, and potentially as part of rented space in studios. I hope to find a way to work with children AND adults (so would love for logo to be appealing to both), but current focus is with children based on need and demand in the community. yoga for children also compliments my backround as a pediatrician/neonatologist, and I greatly miss interacting with children. I also want to emphasize a yoga/movement practice that is focused more on what one feels internally through movement. NOT what one looks like asthetically. I believe in removing all mirrors from yoga/movement practice. It should be an experience of movement/poses/yoga through appropriate cueing and education. It is not about the details of how far the knee should bend, or how high the leg should be. Focusing on foudation first, core, then core engagement and ultimately expression of poses/movements. A focus on strength, stability and mobility, not just flexibility, which is the common perception/association with yoga. I also want individuals to learn to be an advocate of their own health. Through guidance, I hope for individuals to connect with their body so they know themselves so well to be able to advocate for themselves in the modern healthcare world. This internal experience and connection is so essential in a world where modern medicine has become a business and it is all about making a dollar. the connection with patients is lost, and individuals need to learn to empower themselves and through their new found voice to be able to articulate what is wrong.<br/>Does your company have a tagline or slogan that should be included with the logo? "Practice Radiant Movement"<br/>What do you hope your company can be known for? Accessible yoga for a sustained practice. A guided movement practice where one gains information and knowledge of oneself through a mind/body connection. For one feel good physically with a new awaraness of their internal radiance that exists in all beings. Physical rejuvenation egnites a light and increases energy to flow through the physical body, which ultimately tranlates into works of kindness for others and out in the world. <br/>What color palettes might you prefer? why? love the colors currently chosen<br/>Where will the logo be primarily used? initially business cards, but hopefully future websites, t-shirts, and potentially local magazine adds. Also starting with a small couple of banners for community events in the area. I currently practice as a nomad out of my car :)<br/>Are there any elements you would prefer to see in the logo? Movement. A modern depiction of a human body/figure practicing movement. Hoping to avoid a stereotypical yoga pose per say, just because I want to people to think of it more of a movement practice with yoga roots. Modern yoga. There are elements of breathing and connecting with oneself through the flow of breath and movement, but I do not focus on the meditative/cerebral aspect of the yoga practice. What I teach is almost reaching a meditative state through movement. I personally don't practice, nor resonate with just seated meditation. just not my thing :)<br/>In your opinion, what defines a well-designed logo? curiosity. enough info for individuals to think they know what it means, but want to know more. invokes curiosity, but not too abstract. Reproducible. not too complicated. I want also to invoke a community feel, so a design that appeals to all people within a community. <br/>What is your preference in reference to icons, typography, spokespeople (characters), etc.? modern design. I love the idea of a logo for my purposes, to invoke a sense of movement from within. So not too static. <br/>What words or icons must be included in the logo? movement with yoga roots. <br/>What logos do you like and why? A representation, but not exact. I think some ambiguity is intriguing for others, and also memorable. I want it to be an artistic representation of movement/yoga<br/>What logos do you dislike and why? too busy, too loud. <br/>In your opinion, what is the primary purpose for a logo? association<br/>Who is the primary target audience? (who is most likely to use your services/product?) Children and their parents, but ultimately to expand into teaching adults. I even have aspirations of prenatal and post-natal yoga. Potentially incorporating infants. <br/>Who currently uses your product the most? n/a (working in schools/daycare currently. It is currently all volunteer)<br/>Are you pleased with the range of people your company serves? n/a<br/>Are you looking to expand, modify, or completely change your target audience? or will it remain the same? yes! expand into an adult audience. <br/>How do you plan to focus on your target audience? currently by working through schools and daycares. hopefully ultimately through after school care programs and then offering kid yoga in an existing yoga studio (working on this with Q Studio in Ridgeland, currently)<br/>What are your main forms of advertising? word of mouth, schools, daycares. Happy kids talking to their parents about the yoga class they took and happy teachers :)<br/>How do most customers find out about your company?<br/>Which gender are you targeting? All genders! However, with kid yoga, often the maternal individual in the child's life is more involved with decision making as far as extracurricular activities

Target Market(s)

individuals and families interested in wellness and feeling great

Contact Information for Business Card

Dana Whitford
Yoga Instructor
RYT-200, RCYT

certified yoga teacher for adults and children

Colors

Designer to choose colors to be used in the design.

Requirements
Must have
• "Practice Radiant Movement"
Nice to have
• logo with same colors

```html
<!DOCTYPE html>
<html lang="en">
<head>
<meta charset="utf-8">
<title>Glowfield Studios – Business Card</title>
<link href="https://fonts.googleapis.com/css2?family=Montserrat:wght@400;600&family=Quicksand:wght@500&display=swap" rel="stylesheet">
<style>
  :root{
    --backdrop:#303030;
    --card-white:#ffffff;
    --teal:#64c8d0;
    --sun:#f6d93b;
    --ink:#2f2f2f;
    --grey:#7a7a7a;
  }
  html,body{margin:0;padding:0;overflow:hidden;}
  body{width:1200px;height:866px;background:var(--backdrop);position:relative;font-family:"Montserrat",sans-serif;}
  .card{position:absolute;top:278px;width:540px;height:310px;box-shadow:0 14px 30px rgba(0,0,0,.45);overflow:hidden;}
  .card--front{left:30px;background:var(--card-white);}
  .card--back{left:630px;background:var(--teal);}
  .card__bands{position:absolute;left:0;bottom:0;width:540px;height:40px;}
  .person{position:absolute;left:34px;top:32px;}
  .person__name{margin:0;font-weight:600;font-size:20px;letter-spacing:1px;color:var(--sun);text-transform:uppercase;}
  .person__role{margin:2px 0 0;font-size:14px;color:var(--ink);}
  .contact{position:absolute;left:34px;top:120px;margin:0;padding:0;list-style:none;font-size:14px;color:var(--ink);line-height:21px;}
  .contact li{display:flex;align-items:center;gap:7px;}
  .contact svg{width:12px;height:12px;flex:none;}
  .address{position:absolute;left:34px;top:196px;margin:0;font-size:14px;line-height:20px;color:var(--ink);font-style:normal;}
  .brand{position:absolute;display:flex;align-items:center;gap:10px;}
  .card--front .brand{left:312px;top:92px;}
  .card--back .brand{left:182px;top:98px;}
  .brand__dot{width:34px;height:34px;border-radius:50%;background:var(--sun);}
  .brand__name{font-family:"Quicksand",sans-serif;font-weight:500;font-size:30px;color:var(--grey);}
  .card--back .brand__name{color:var(--card-white);}
  .social{position:absolute;right:34px;bottom:56px;display:flex;gap:6px;}
  .social span{width:20px;height:20px;border:2px solid var(--ink);border-radius:50%;box-sizing:border-box;}
</style>
</head>
<body>
  <section class="card card--front">
    <div class="person">
      <h1 class="person__name">Dana Whitford</h1>
      <p class="person__role">Yoga Instructor</p>
    </div>
    <ul class="contact">
      <li><svg viewBox="0 0 12 12"><path d="M2 1h3l1 3-2 1a7 7 0 0 0 3 3l1-2 3 1v3c-6 1-10-3-9-9z" fill="#f6d93b"/></svg>044-555 010 234</li>
      <li><svg viewBox="0 0 12 12"><rect x="0.5" y="2" width="11" height="8" fill="#f6d93b"/><path d="M1 2.5l5 4 5-4" stroke="#fff" fill="none"/></svg>hello@glowfield.example</li>
      <li><svg viewBox="0 0 12 12"><circle cx="6" cy="6" r="5.5" fill="#f6d93b"/></svg>www.glowfield.example</li>
    </ul>
    <address class="address">27, Maple Row Lane<br>Country Name, 123456</address>
    <div class="brand"><span class="brand__dot"></span><span class="brand__name">Glowfield</span></div>
    <div class="social" aria-label="Social profiles"><span></span><span></span><span></span><span></span></div>
    <svg class="card__bands" viewBox="0 0 540 40" preserveAspectRatio="none">
      <polygon points="0,26 300,26 300,40 0,40" fill="#f6d93b"/>
      <polygon points="300,22 540,22 540,40 300,40" fill="#64c8d0"/>
    </svg>
  </section>

  <section class="card card--back">
    <div class="brand"><span class="brand__dot"></span><span class="brand__name">Glowfield</span></div>
  </section>
</body>
</html>
```